Harrow Grading LLC business card design

Excavation company business cards

Contact Information for Business Card

Harrow Grading LLC cell phone 208-417-6290 office phone 208-319-4856 harrowgradingllc@maplecove.com Driveways, site prep, retaining walls, septic systems, rock delivery

Colors

Designer to choose colors to be used in the design.

```html
<!DOCTYPE html>
<html lang="en">
<head>
<meta charset="utf-8">
<title>Harrow Grading LLC – Business Cards</title>
<link rel="stylesheet" href="https://fonts.googleapis.com/css2?family=Michroma&family=Arimo:wght@400&display=swap">
<style>
  :root {
    --bg: #0e0e0f;
    --card: #2b2b2d;
    --card-edge: #e8731f;
    --orange: #f07a22;
    --text-light: #d9d9d9;
    --text-muted: #8a8a8c;
    --rule: #5a5a5c;
    --emboss: #4a4a4d;
  }
  * { margin: 0; padding: 0; box-sizing: border-box; }
  html, body {
    width: 1200px; height: 820px; overflow: hidden;
    background: var(--bg);
  }
  .canvas {
    position: relative; width: 1200px; height: 820px;
    display: flex; align-items: center; justify-content: center; gap: 40px;
  }
  .card {
    position: relative; width: 560px; height: 320px;
    background: var(--card);
    border: 2px solid var(--card-edge);
    font-family: "Arimo", Arial, sans-serif;
    color: var(--text-light);
  }
  /* Front */
  .brand {
    position: absolute; top: 64px; right: 44px;
    display: flex; align-items: center; gap: 10px;
    font-family: "Michroma", sans-serif;
    font-size: 22px; color: var(--orange); letter-spacing: 1px;
  }
  .brand-mark { width: 14px; height: 14px; background: var(--orange); }
  .address {
    position: absolute; top: 112px; right: 44px;
    text-align: right; font-size: 14px; line-height: 17px; color: var(--text-light);
  }
  .divider {
    position: absolute; height: 1px; background: var(--rule);
  }
  .divider--main { left: 40px; right: 44px; top: 178px; }
  .person { position: absolute; left: 40px; top: 196px; }
  .person-name {
    font-family: "Michroma", sans-serif; font-size: 17px;
    color: var(--orange); letter-spacing: .5px;
  }
  .person-title { font-size: 15px; margin-top: 2px; }
  .divider--contact { left: 40px; width: 200px; top: 246px; }
  .contacts {
    position: absolute; left: 40px; top: 254px;
    list-style: none; font-size: 15px; line-height: 19px;
  }
  .contacts li { display: flex; align-items: center; gap: 8px; }
  .contacts svg { width: 13px; height: 13px; fill: none; stroke: var(--orange); stroke-width: 1.8; }
  /* Back */
  .card--back { display: flex; flex-direction: column; align-items: center; justify-content: center; }
  .back-brand {
    display: flex; align-items: center; gap: 12px;
    font-family: "Michroma", sans-serif; font-size: 28px;
    color: var(--emboss); letter-spacing: 1px;
  }
  .back-brand .brand-mark { width: 18px; height: 18px; background: var(--emboss); }
  .services {
    margin-top: 26px; text-align: center;
    font-size: 15px; line-height: 19px; color: var(--text-light);
  }
  .dot { color: var(--orange); }
</style>
</head>
<body>
<main class="canvas">
  <section class="card card--front" aria-label="Business card front">
    <div class="brand"><span class="brand-mark"></span>HARROW GRADING LLC</div>
    <p class="address">421, Address line<br>goes here, 45452<br>Country Name</p>
    <div class="divider divider--main"></div>
    <div class="person">
      <p class="person-name">MARCUS HALE</p>
      <p class="person-title">Managing Director</p>
    </div>
    <div class="divider divider--contact"></div>
    <ul class="contacts">
      <li><svg viewBox="0 0 14 14"><rect x="3.5" y="1" width="7" height="12" rx="1.2"/><line x1="6" y1="11" x2="8" y2="11"/></svg>208-417-6290</li>
      <li><svg viewBox="0 0 14 14"><path d="M2 2.5 L4.5 1.5 L6 4.5 L4.5 5.5 Q5.5 8 8.5 9.5 L9.5 8 L12.5 9.5 L11.5 12 Q5 12 2 2.5 Z"/></svg>208-319-4856</li>
      <li><svg viewBox="0 0 14 14"><rect x="1" y="3" width="12" height="8"/><polyline points="1,3 7,8 13,3"/></svg>harrowgradingllc@maplecove.com</li>
    </ul>
  </section>

  <section class="card card--back" aria-label="Business card back">
    <div class="back-brand"><span class="brand-mark"></span>HARROW GRADING LLC</div>
    <p class="services">
      Driveways <span class="dot">●</span> Site prep <span class="dot">●</span> Retaining walls<br>
      Septic systems <span class="dot">●</span> Rock delivery
    </p>
  </section>
</main>
</body>
</html>
```